sticker for cleaning products

it is in the bottle. products are bio-cleaner. Toilet Cleaner - yellow Sanitary Cleaner - orange Glass Cleaner - light blue All purpose cleaner - green Hand Soap - cream Detergent - olive Detergent - rose bottles is used RUNDA: https://glasbehalterwerk.de/katalog/#Runda shape of the sticker is not geometric. It's something like a cloud / leaf / drop / ?? the sticker has an inner space with only the product name and color. the sticker has an outer space. here we want to mark out "powered by KORVINEL" (our company name, find logo attached)

```html
<!DOCTYPE html>
<html lang="en">
<head>
<meta charset="utf-8">
<title>Sanitary Cleaner – Bottle Sticker</title>
<link rel="stylesheet" href="https://fonts.googleapis.com/css2?family=Bebas+Neue&family=Montserrat:wght@500;800&display=swap">
<style>
  :root {
    --paper: #ffffff;
    --leaf-back: #f3a726;
    --drop-top: #f6ad2a;
    --drop-bottom: #e5831a;
    --label-fill: #ffffff;
    --ink: #111111;
    --shadow: #6a3a0c;
    --brand-grey: #4a4a4a;
    --brand-tan: #a9805d;
  }
  html, body {
    margin: 0;
    padding: 0;
    width: 1200px;
    height: 2258px;
    overflow: hidden;
    background: var(--paper);
  }
  .sticker {
    display: block;
    width: 1200px;
    height: 2258px;
  }
  .product-name {
    font-family: "Bebas Neue", "Oswald", sans-serif;
    fill: var(--ink);
    font-size: 79px;
  }
  .powered-by {
    font-family: "Montserrat", sans-serif;
    font-weight: 800;
    font-size: 11px;
    fill: var(--ink);
  }
  .brand-name {
    font-family: "Montserrat", sans-serif;
    font-weight: 500;
    font-size: 22px;
    letter-spacing: 11px;
    fill: var(--brand-grey);
  }
  .brand-dot { fill: var(--brand-tan); }
</style>
</head>
<body>
<svg class="sticker" viewBox="0 0 438 824" xmlns="http://www.w3.org/2000/svg" aria-label="Sanitary Cleaner sticker, powered by KORVINEL">
  <defs>
    <linearGradient id="drop-gradient" x1="0" y1="0" x2="0.3" y2="1">
      <stop offset="0" stop-color="var(--drop-top)"/>
      <stop offset="1" stop-color="var(--drop-bottom)"/>
    </linearGradient>
    <filter id="soft-shadow" x="-20%" y="-20%" width="140%" height="140%">
      <feDropShadow dx="0" dy="6" stdDeviation="6" flood-color="var(--shadow)" flood-opacity="0.4"/>
    </filter>
    <filter id="inner-shadow" x="-20%" y="-20%" width="140%" height="140%">
      <feDropShadow dx="0" dy="4" stdDeviation="5" flood-color="#000" flood-opacity="0.3"/>
    </filter>
  </defs>

  <path class="leaf-back" fill="var(--leaf-back)" filter="url(#soft-shadow)"
        d="M85,45 C200,80 330,200 360,360 C380,470 330,550 240,550 C120,550 25,470 22,330 C20,230 50,130 85,45 Z"/>

  <path class="drop-outer" fill="url(#drop-gradient)" filter="url(#soft-shadow)"
        d="M252,2 C320,90 440,190 438,340 C437,450 355,530 255,530 C150,530 70,450 70,340 C70,200 190,90 252,2 Z"/>

  <path class="drop-inner" fill="var(--label-fill)" filter="url(#inner-shadow)"
        d="M250,55 C300,120 400,210 400,330 C400,425 335,492 255,492 C170,492 108,425 108,330 C108,215 200,125 250,55 Z"/>

  <text class="product-name" x="258" y="310" text-anchor="middle" textLength="245" lengthAdjust="spacingAndGlyphs">SANITARY</text>
  <text class="product-name" x="257" y="406" text-anchor="middle" textLength="225" lengthAdjust="spacingAndGlyphs">CLEANER</text>

  <text class="powered-by" x="97" y="662">powered by</text>
  <circle class="brand-dot" cx="222" cy="656" r="32"/>
  <text class="brand-name" x="226" y="721" text-anchor="middle">KORVINEL</text>
</svg>
</body>
</html>
```